Meridale Partners Website

Meridale Partners (MP) provide Analytics & Enterprise Performance Management (EPM) advisory & consultancy services. We are passionate about data and making a difference for our clients by working in partnership with them, helping them on their journey to becoming an Meridale Partner. We deliver insights which give our clients a competitive edge and a much deeper understanding of their organisation.

We need a website which shows who we are, what we do and how we do it.

www.meridale-partners.example is our very basic website at the moment. We want to completely revamp it with a corporate look

```html
<!DOCTYPE html>
<html lang="en">
<head>
<meta charset="utf-8">
<title>Meridale Partners</title>
<link rel="stylesheet" href="https://fonts.googleapis.com/css2?family=Montserrat:wght@400;500;600;700;800&display=swap">
<style>
:root{
  --navy:#27526b;
  --orange:#e07b4c;
  --white:#ffffff;
  --text:#2f3d4a;
  --pale:#f6f9fc;
  --footer:#eef3f8;
  --bar:#dde6ee;
}
*{margin:0;padding:0;box-sizing:border-box}
html,body{width:1200px;height:2646px;overflow:hidden}
body{font-family:'Montserrat',sans-serif;color:var(--text);background:var(--white);position:relative}
.abs{position:absolute}
.btn{position:absolute;background:var(--orange);color:var(--white);font-weight:800;text-transform:uppercase;display:flex;align-items:center;justify-content:center;letter-spacing:.2px}

/* nav */
.nav{position:absolute;left:0;top:0;width:1200px;height:64px;background:var(--white)}
.nav a{position:absolute;top:30px;font-size:15px;font-weight:500;color:var(--navy);text-decoration:none;letter-spacing:.3px}
.nav a.active{color:var(--orange)}
.nav .sep{position:absolute;top:26px;width:2px;height:26px;background:var(--navy)}
.brand{position:absolute;left:509px;top:20px;display:flex;align-items:center;gap:10px}
.brand .dot{width:44px;height:44px;border-radius:50%;border:7px solid var(--navy)}
.brand .name{font-size:17px;font-weight:600;color:var(--navy);line-height:18px;letter-spacing:.8px}

/* hero */
.hero{position:absolute;left:0;top:64px;width:1200px;height:616px;background:linear-gradient(180deg,#3a4f66 0%,#6c7d8c 30%,#4b6377 60%,#2e465a 100%)}
.hero-photo{position:absolute;inset:0;background:radial-gradient(ellipse 260px 240px at 600px 150px,rgba(244,170,90,.85),rgba(200,150,110,.35) 60%,transparent 100%),linear-gradient(90deg,rgba(30,50,70,.6),transparent 30%,transparent 70%,rgba(30,50,70,.6))}
.hero h1{position:absolute;left:131px;top:210px;font-size:40px;line-height:44px;font-weight:800;color:var(--white);letter-spacing:.5px}
.hero p{position:absolute;left:132px;top:312px;font-size:23px;line-height:29px;color:var(--white);font-weight:500}

/* who */
.who{position:absolute;left:0;top:680px;width:1200px;height:763px;background:linear-gradient(180deg,#fff 0%,#f4f9fd 45%,#eaf4fb 100%)}
.who .mark{position:absolute;left:212px;top:70px;width:270px;height:270px;border-radius:50%;border:36px solid var(--navy)}
.who .rule{position:absolute;left:557px;top:60px;width:2px;height:305px;background:var(--navy)}
.eyebrow{font-size:22px;font-weight:800;color:var(--navy);letter-spacing:.3px}
.eyebrow span{color:var(--orange)}
.who .eyebrow{position:absolute;left:627px;top:52px}
.who .eyebrow::after{content:"";position:absolute;left:0;top:32px;width:58px;height:3px;background:var(--orange)}
.who h2{position:absolute;left:626px;top:104px;font-size:24px;font-weight:800;color:var(--navy);letter-spacing:.3px}
.who h2 span{color:var(--orange)}
.who .copy{position:absolute;left:627px;top:164px;width:385px;font-size:16.5px;line-height:25.6px;color:var(--text)}
.who-art{position:absolute;left:0;top:380px;width:1200px;height:383px;background:linear-gradient(180deg,rgba(220,238,250,0) 0%,#dcedf8 35%,#d3e8f6 100%)}

/* what */
.what{position:absolute;left:0;top:1443px;width:1200px;height:484px;background:var(--pale)}
.what .eyebrow{position:absolute;left:0;width:1200px;top:38px;text-align:center;font-size:25px}
.what .bar{position:absolute;left:588px;top:83px;width:28px;height:3px;background:var(--orange)}
.card{position:absolute;top:117px;width:295px;height:322px;border:1px solid var(--navy);background:var(--white);text-align:center}
.card svg{position:absolute;left:115px;top:22px}
.card h3{position:absolute;left:0;width:100%;top:114px;font-size:15.5px;font-weight:800;color:var(--navy)}
.card p{position:absolute;left:38px;width:218px;top:152px;font-size:13.3px;line-height:17.7px;color:var(--text)}
.card.wide p{left:34px;width:226px}
.card.dark{background:var(--navy)}
.card.dark h3,.card.dark p{color:var(--white)}
.card.dark p{left:32px;width:229px}
.card .btn{left:101px;top:260px;width:92px;height:28px;font-size:9.5px}

/* how */
.how{position:absolute;left:0;top:1927px;width:1200px;height:528px;background:var(--navy)}
.how-photo{position:absolute;left:145px;top:48px;width:480px;height:440px;border-radius:48% 52% 46% 54% / 44% 50% 50% 56%;background:linear-gradient(135deg,#3b3f9e 0%,#2a3f8e 60%,#1d2c6a 100%)}
.how h2{position:absolute;left:675px;top:52px;font-size:25px;font-weight:800;color:var(--white)}
.how .bar{position:absolute;left:676px;top:96px;width:28px;height:3px;background:var(--orange)}
.how h4{position:absolute;left:678px;font-size:16.5px;line-height:24px;font-weight:700;color:var(--white)}
.how p{position:absolute;left:678px;width:400px;font-size:13.6px;line-height:17.8px;color:#e6edf2}

/* footer */
.footer{position:absolute;left:0;top:2455px;width:1200px;height:158px;background:var(--footer)}
.f-brand{position:absolute;left:133px;top:40px;display:flex;align-items:center;gap:18px}
.f-brand .dot{width:82px;height:82px;border-radius:50%;border:13px solid var(--navy)}
.f-brand .name{font-size:28px;line-height:31px;font-weight:600;color:var(--navy);letter-spacing:1px}
.f-rule{position:absolute;left:463px;top:40px;width:2px;height:82px;background:var(--navy)}
.badge{position:absolute;left:493px;top:40px;width:72px;height:20px;background:#d9644f;border-radius:3px}
.f-text{position:absolute;font-size:13.5px;line-height:20px;color:var(--text)}
.social{position:absolute;top:83px;width:38px;height:38px;border-radius:50%;background:#d7dee5}
.copyright{position:absolute;left:0;top:2613px;width:1200px;height:33px;background:var(--bar);text-align:center;font-size:12px;line-height:33px;color:var(--text)}
</style>
</head>
<body>

<header class="nav">
  <a class="active" style="left:297px">HOME</a>
  <div class="sep" style="left:361px"></div>
  <a style="left:380px">SERVICES</a>
  <div class="brand"><div class="dot"></div><div class="name">MERIDALE<br>PARTNERS</div></div>
  <a style="left:733px">ABOUT US</a>
  <div class="sep" style="left:834px"></div>
  <a style="left:851px">CONTACT US</a>
</header>

<section class="hero">
  <div class="hero-photo" role="img" aria-label="Businessman climbing a staircase towards a glowing city skyline, with rising arrows and bar charts"></div>
  <h1>MERIDALE<br>PARTNERS</h1>
  <p>Data Analytics &amp; Epm<br>Consulting Services</p>
  <div class="btn" style="left:138px;top:400px;width:124px;height:38px;font-size:13px">Read More</div>
</section>

<section class="who">
  <div class="who-art" role="img" aria-label="Illustration of hands typing on a laptop beneath a rising line chart with business icons"></div>
  <div class="mark"></div>
  <div class="rule"></div>
  <div class="eyebrow"><span>WHO</span> WE ARE</div>
  <h2>MERIDALE <span>PARTNERS</span></h2>
  <p class="copy">MP are a Data Analytics &amp; EPM company, specialising in the implementation and support of Business Intelligence, EPM and Data Analytics business solutions, both in the Cloud and on-premise.</p>
  <div class="btn" style="left:627px;top:329px;width:116px;height:35px;font-size:12.5px">Read More</div>
</section>

<section class="what">
  <div class="eyebrow">WHAT WE <span>DO</span></div>
  <div class="bar"></div>

  <div class="card" style="left:131px">
    <svg width="66" height="66" viewBox="0 0 66 66"><circle cx="27" cy="27" r="21" fill="none" stroke="var(--navy)" stroke-width="4"/><circle cx="27" cy="27" r="16" fill="var(--orange)"/><path d="M20 34V28M25 34V24M30 34V21M35 34V26" stroke="#fff" stroke-width="3"/><path d="M42 42L60 60" stroke="var(--navy)" stroke-width="7" stroke-linecap="round"/></svg>
    <h3>ADVISE &amp; ARCHITECT</h3>
    <p>Helping our customers understand the art of the possible and safeguarding their investments by overseeing implementations.</p>
    <div class="btn">Read More</div>
  </div>

  <div class="card dark" style="left:454px">
    <svg width="66" height="66" viewBox="0 0 66 66"><path d="M33 4A21 21 0 0 0 21 42V50H45V42A21 21 0 0 0 33 4Z" fill="#fff"/><path d="M23 55H43M25 60H41" stroke="var(--orange)" stroke-width="3"/></svg>
    <h3>DESIGN &amp; IMPLEMENT</h3>
    <p>Working with the project management team, through each stage of the project, with clearly defined deliverables and well exercised plans to deliver them.</p>
    <div class="btn">Read More</div>
  </div>

  <div class="card wide" style="left:775px">
    <svg width="66" height="66" viewBox="0 0 66 66"><path d="M12 6H40L50 16V58H12Z" fill="#fff" stroke="var(--navy)" stroke-width="4"/><path d="M19 22H42M19 29H42M19 36H38M19 43H34" stroke="var(--navy)" stroke-width="3"/><circle cx="49" cy="50" r="9" fill="none" stroke="var(--orange)" stroke-width="6" stroke-dasharray="4 3"/></svg>
    <h3>OPTIMISE &amp; MANAGE</h3>
    <p>Our Managed Services delivers proactive, on-demand support for EPM and Data Analytics environments:</p>
    <div class="btn">Read More</div>
  </div>
</section>

<section class="how">
  <div class="how-photo" role="img" aria-label="Hand with a stylus over a tablet showing financial analysis charts"></div>
  <h2>HOW WE DO IT</h2>
  <div class="bar"></div>
  <h4 style="top:136px">Analytics &amp; Enterprise<br>Performance Management</h4>
  <p style="top:205px">There are many variations of passages of Lorem Ipsum available, but the majority have suffered alteration in some form, by injected humour, or randomised words which don't look even slightly believable.</p>
  <h4 style="top:309px">Advisory &amp; Consultancy</h4>
  <p style="top:341px">There are many variations of passages of Lorem Ipsum available, but the majority have suffered alteration in some form, by injected humour, or randomised words which don't look even slightly believable.</p>
  <div class="btn" style="left:681px;top:439px;width:122px;height:37px;font-size:13px">Read More</div>
</section>

<footer class="footer">
  <div class="f-brand"><div class="dot"></div><div class="name">MERIDALE<br>PARTNERS</div></div>
  <div class="f-rule"></div>
  <div class="badge"></div>
  <div class="f-text" style="left:493px;top:88px">14 Harbour Row,<br>Eastgate, Dunmore D09 QX41</div>
  <div class="f-text" style="left:725px;top:88px">Email us<br>info@meridale-partners.example</div>
  <div class="f-text" style="left:974px;top:40px">Follow us</div>
  <div class="social" style="left:971px"></div>
  <div class="social" style="left:1027px"></div>
</footer>
<div class="copyright">Copyright © 2022 All Rights Reserved</div>

</body>
</html>
```